LEARN Business Skills so you can Earn a good living

size of the poster is 8”x 10.75" plus 0.25" bleed.
Please leave 1 inch on the bottoum for footer
I want a design a poster that will attract people's attention.
I appreciate a creative ad however the ad should not take away from being able to clearly read the text.
-I also appreciate a simple creative ad that is not too busy.
-you can use graphics, vectors, or pictures of real people.
-however, if you use real people it should be a white male that is wearing a white shirt and look like a professional person.

Target Market(s)

Potential young business people

Industry/Entity Type

education

Requirements
Must have
• easy to read the text
Nice to have
• I would like a "creative" simple ad that is easy to be read
Should not have
• pictures of women

```html
<!DOCTYPE html>
<html lang="en">
<head>
<meta charset="utf-8">
<title>Learn It To Earn It – Business Enrichment Course</title>
<link href="https://fonts.googleapis.com/css2?family=Bebas+Neue&display=swap" rel="stylesheet">
<style>
  :root {
    --page: #ffffff;
    --red: #c8171c;
    --red-deep: #a51216;
    --white: #ffffff;
    --yellow: #ffe600;
  }
  html, body {
    margin: 0;
    padding: 0;
    width: 1200px;
    height: 1200px;
    overflow: hidden;
    background: var(--page);
  }
  .poster {
    position: absolute;
    left: 281px;
    top: 161px;
    width: 645px;
    height: 886px;
    background:
      radial-gradient(ellipse at 50% 45%, var(--red) 55%, var(--red-deep) 100%);
    font-family: "Bebas Neue", "Oswald", sans-serif;
    color: var(--white);
    overflow: hidden;
  }
  .poster > * { position: absolute; margin: 0; white-space: nowrap; }
  .headline {
    left: 75px;
    top: 58px;
    font-size: 123px;
    line-height: 0.8;
    font-weight: 400;
  }
  .headline-box {
    left: 66px;
    top: 149px;
    width: 411px;
    height: 104px;
    background: var(--white);
    border-radius: 8px;
  }
  .headline-boxed {
    left: 75px;
    top: 159px;
    color: var(--red);
  }
  .course-title {
    left: 193px;
    top: 277px;
    font-size: 57px;
    line-height: 0.8;
    font-weight: 400;
  }
  .course-title .accent {
    display: block;
    margin-top: 9px;
    font-size: 61px;
    color: var(--yellow);
  }
  .rule {
    left: 66px;
    width: 147px;
    height: 7px;
    background: var(--yellow);
  }
  .rule-top { top: 386px; }
  .rule-bottom { top: 481px; }
  .promise {
    left: 66px;
    top: 406px;
    font-size: 39px;
    line-height: 0.8;
  }
  .promise span { display: block; margin-bottom: 6px; }
  .skills-title {
    left: 193px;
    top: 508px;
    font-size: 53px;
    line-height: 0.8;
    font-weight: 400;
  }
  .skills-title .accent {
    display: block;
    margin-top: 5px;
    color: var(--yellow);
  }
  .benefits {
    left: 66px;
    top: 614px;
    list-style: none;
    padding: 0;
    font-size: 29px;
    line-height: 0.8;
  }
  .benefits li {
    position: relative;
    padding-left: 30px;
    height: 23px;
    margin-bottom: 6.5px;
  }
  .benefits li::before {
    content: "";
    position: absolute;
    left: 0;
    top: 8px;
    width: 17px;
    height: 6px;
    background: var(--yellow);
  }
  .topics {
    left: 0;
    top: 705px;
    width: 645px;
    text-align: center;
    font-size: 14px;
    line-height: 19px;
    white-space: normal;
  }
  .topics span { display: block; }
  .footer-rule {
    left: 261px;
    top: 780px;
    width: 122px;
    height: 1px;
    background: var(--yellow);
  }
</style>
</head>
<body>
  <main class="poster">
    <h1 class="headline">Learn it</h1>
    <div class="headline-box"></div>
    <p class="headline headline-boxed">To earn it</p>

    <h2 class="course-title">Business<span class="accent">Enrichment course</span></h2>

    <div class="rule rule-top"></div>
    <p class="promise"><span>A proven success of helping</span><span>people in their livelihoods</span></p>
    <div class="rule rule-bottom"></div>

    <h2 class="skills-title">Business skills<span class="accent">that will help you</span></h2>

    <ul class="benefits">
      <li>Get a quality job</li>
      <li>Start/grow your business</li>
      <li>Increase your salary</li>
    </ul>

    <p class="topics">
      <span>Business Administration - Small Business Management - Finance - Investments - Computers - Accounting - Sales -</span>
      <span>Marketing - Project Management Interviewing Skills - Business Law - Negotiation - Public Speaking - Import/Export -</span>
      <span>Information Technology - Distribution - Marketing - LedgerPro - Real Estate - Health Care - Management - Shopwave</span>
    </p>

    <div class="footer-rule"></div>
  </main>
</body>
</html>
```